Business card por a urban DJ, up scale audience target

Need a sober design, modern, conservative colors but i can consider some options, y play rnb, hip hop, EDM and top40.

Business card for contact and personal info, double sided, use logo attrached please; im 42 so i need a card acording to my age an target audience.

Target Market(s)

Adult people, up scale audience

Industry/Entity Type

Music Download

Contact Information for Business Card

Cel (318) 4207265518 www.lumadrift.com

Requirements
Must have
• open mind
Nice to have
• open mind
Should not have
• DJ

```html
<!DOCTYPE html>
<html lang="en">
<head>
<meta charset="utf-8">
<title>Lumadrift Business Card</title>
<link href="https://fonts.googleapis.com/css2?family=Jost:wght@400;500;600&display=swap" rel="stylesheet">
<style>
  :root {
    --backdrop: #e9e7e3;
    --card-white: #ffffff;
    --band-dark: #1b1b1b;
    --band-mid: #2d2d2d;
    --card-back: #1c1c1c;
    --ink: #222222;
    --text-light: #f2f2f2;
    --divider: #6a6a6a;
  }
  html, body {
    margin: 0;
    padding: 0;
    width: 1200px;
    height: 950px;
    overflow: hidden;
    background: var(--backdrop);
  }
  .canvas {
    width: 1200px;
    height: 950px;
    display: flex;
    flex-direction: column;
    align-items: center;
    justify-content: center;
    gap: 36px;
  }
  .business-card {
    width: 740px;
    height: 423px;
    box-shadow: 0 14px 32px rgba(0,0,0,0.22);
    font-family: "Jost", sans-serif;
    overflow: hidden;
  }
  .card-front {
    background: var(--card-white);
    display: flex;
    flex-direction: column;
  }
  .card-back {
    background: var(--card-back);
  }
  .brand-area {
    flex: 1;
    display: flex;
    align-items: center;
    justify-content: center;
  }
  .brand-name {
    font-family: "Jost", sans-serif;
    font-weight: 600;
    font-size: 88px;
    letter-spacing: 6px;
    color: var(--ink);
    margin: 0;
  }
  .contact-band {
    height: 148px;
    background: linear-gradient(90deg, var(--band-dark), var(--band-mid) 60%, var(--band-dark));
    display: flex;
    align-items: center;
    justify-content: center;
    color: var(--text-light);
  }
  .identity {
    text-align: right;
    padding-right: 26px;
  }
  .identity-name {
    font-size: 22px;
    font-weight: 600;
    letter-spacing: 1px;
    margin: 0;
  }
  .identity-role {
    font-size: 17px;
    font-weight: 400;
    margin: 4px 0 0;
  }
  .band-divider {
    width: 1px;
    height: 80px;
    background: var(--divider);
  }
  .contact-list {
    list-style: none;
    margin: 0;
    padding: 0 0 0 26px;
    font-size: 17px;
    font-weight: 400;
  }
  .contact-item {
    display: flex;
    align-items: center;
    gap: 12px;
    line-height: 32px;
  }
  .contact-icon {
    width: 15px;
    height: 15px;
    flex: none;
  }
</style>
</head>
<body>
  <main class="canvas">
    <article class="business-card card-front">
      <section class="brand-area">
        <h1 class="brand-name">LUMA</h1>
      </section>
      <section class="contact-band">
        <div class="identity">
          <p class="identity-name">MARCUS VELL</p>
          <p class="identity-role">CEO/FOUNDER</p>
        </div>
        <div class="band-divider"></div>
        <ul class="contact-list">
          <li class="contact-item">
            <svg class="contact-icon" viewBox="0 0 20 20" aria-hidden="true">
              <rect x="4" y="2" width="12" height="16" rx="2" fill="none" stroke="#f2f2f2" stroke-width="2"/>
            </svg>
            (318) 4207265518
          </li>
          <li class="contact-item">
            <svg class="contact-icon" viewBox="0 0 20 20" aria-hidden="true">
              <circle cx="10" cy="10" r="8" fill="#f2f2f2"/>
              <path d="M2 10h16M10 2c-4 4-4 12 0 16M10 2c4 4 4 12 0 16" fill="none" stroke="#1b1b1b" stroke-width="1.4"/>
            </svg>
            www.lumadrift.com
          </li>
        </ul>
      </section>
    </article>
    <article class="business-card card-back" aria-label="Card back, plain dark"></article>
  </main>
</body>
</html>
```